To design a brand identity that is simple and creative with 'Corvane' as the brand name, I like modern simple fonts like helvetica neue, I want to print both sides of the card, I am open to dark front and white back, but the design needs to transfer well to letter heads and email signatures, I am looking for sophisticated and elegant, but open minded about clever and off the wall, I do not do 'boring' Corvane Ventures is the mother company for a small group, specialising in Management & consulting, Software development and construction, we have a high level of integrity, we are transparent and accountable for what we do. my images are provided as a guide only, Im not expecting them to be just copied, Im looking for a creator and passionate thinker, who will put life into their work.

Target Market(s)

usually business minded people who are looking for something different in me, such as leadership, confidence and focus with thinking that is per haps a little outside the box..

Industry/Entity Type

Construction

Requirements
Must have
• clean, minmalistic
Nice to have
• custom logo
Should not have
• boring, traditional

```html
<!DOCTYPE html>
<html lang="en">
<head>
<meta charset="utf-8">
<title>Corvane — Business Card</title>
<link rel="stylesheet" href="https://fonts.googleapis.com/css2?family=Inter:wght@300;400&family=Cormorant+Garamond:ital,wght@1,500&display=swap">
<style>
  :root {
    --stage: #3a3534;
    --card-light: #ffffff;
    --card-light-edge: #d9dadb;
    --card-dark: #2b2929;
    --card-dark-glow: #4d4847;
    --accent: #e8623f;
    --accent-red: #e2372a;
    --ink: #262626;
    --ink-soft: #666666;
    --ghost: #d3d4d6;
    --on-dark: #ffffff;
    --on-dark-soft: #dddddd;
    --label: #e6e2e0;
  }
  * { margin: 0; padding: 0; box-sizing: border-box; }
  html, body { width: 1000px; height: 1200px; overflow: hidden; }
  body {
    background: var(--stage);
    font-family: "Inter", "Helvetica Neue", Arial, sans-serif;
    font-weight: 300;
    position: relative;
  }

  .card { position: absolute; width: 740px; height: 456px; overflow: hidden; }

  /* Front */
  .card--front {
    left: 136px; top: 75px;
    background: radial-gradient(ellipse at 45% 45%, var(--card-light) 35%, var(--card-light-edge) 100%);
  }
  .brand { position: absolute; display: flex; align-items: center; }
  .brand__dot { border-radius: 50%; background: var(--accent); flex: none; }
  .card--front .brand { left: 47px; top: 210px; }
  .card--front .brand__dot { width: 42px; height: 42px; margin-right: 22px; }
  .card--front .brand__name { color: var(--accent); font-size: 46px; line-height: 1; letter-spacing: 0.3px; }
  .tagline {
    position: absolute; right: 428px; top: 266px;
    font-family: "Cormorant Garamond", Georgia, serif; font-style: italic; font-weight: 500;
    font-size: 16px; color: var(--ink-soft); white-space: nowrap;
  }
  .ghost-name {
    position: absolute; left: 372px; top: 228px;
    transform: translate(-50%, -50%) rotate(-90deg);
    font-size: 62px; color: var(--ghost); line-height: 1; white-space: nowrap;
  }
  .services-vertical {
    position: absolute; left: 370px; top: 228px;
    transform: translate(-50%, -50%) rotate(-90deg);
    font-size: 15.5px; font-weight: 400; color: var(--ink); white-space: nowrap; letter-spacing: 0.6px;
  }
  .sep { color: var(--accent-red); padding: 0 5px; }
  .contact { position: absolute; left: 454px; top: 136px; color: var(--ink); }
  .contact__name { color: var(--accent-red); font-size: 26px; font-weight: 400; line-height: 1; }
  .contact__role { color: var(--ink-soft); font-size: 16px; font-weight: 400; margin-top: 7px; }
  .contact__list { list-style: none; font-size: 19px; font-weight: 400; margin-top: 8px; }
  .contact__list li { height: 28px; line-height: 28px; }
  .contact__list li.gap { margin-top: 13px; }
  .contact__key { color: var(--accent); margin-right: 6px; }

  /* Back */
  .card--back {
    left: 117px; top: 651px;
    background: radial-gradient(ellipse at 50% 40%, var(--card-dark-glow) 0%, var(--card-dark) 65%);
  }
  .card--back .brand { left: 0; right: 0; top: 187px; justify-content: center; }
  .card--back .brand__dot { width: 92px; height: 92px; margin-right: 24px; box-shadow: 0 0 0 3px var(--on-dark); }
  .card--back .brand__name { color: var(--on-dark); font-size: 84px; line-height: 1; }
  .services {
    position: absolute; left: 0; right: 0; top: 297px; text-align: center;
    color: var(--on-dark-soft); font-size: 16px; font-weight: 400; letter-spacing: 1px;
  }

  .side-label { position: absolute; color: var(--label); font-size: 20px; font-weight: 400; }
  .side-label--front { left: 811px; top: 570px; }
  .side-label--back { left: 117px; top: 1143px; }
</style>
</head>
<body>
  <section class="card card--front" aria-label="Card front">
    <div class="brand">
      <span class="brand__dot"></span>
      <span class="brand__name">corvane.</span>
    </div>
    <p class="tagline">..in the building business.</p>
    <div class="ghost-name" aria-hidden="true">corvane</div>
    <div class="services-vertical">management<span class="sep">•</span>software<span class="sep">•</span>construction</div>
    <div class="contact">
      <p class="contact__name">Mara Lindell</p>
      <p class="contact__role">client ambassador</p>
      <ul class="contact__list">
        <li><span class="contact__key">c.</span>+61 0400 555 214</li>
        <li><span class="contact__key">e.</span>info@corvane.com.au</li>
        <li class="gap"><span class="contact__key">a.</span>po box 418 perth 6031</li>
        <li><span class="contact__key">w.</span>www.corvane.com.au</li>
      </ul>
    </div>
  </section>
  <p class="side-label side-label--front">Front</p>

  <section class="card card--back" aria-label="Card back">
    <div class="brand">
      <span class="brand__dot"></span>
      <span class="brand__name">corvane.</span>
    </div>
    <p class="services">management<span class="sep">•</span>software<span class="sep">•</span>construction</p>
  </section>
  <p class="side-label side-label--back">Back</p>
</body>
</html>
```